School Poster

Design so that these can be placed in classrooms across the school.

Attached is another design we have had done. Use a similar theme.

Consider using themes from https://corvalhs.edq.example.au/

please edit Binder1 doc.

Students and teachers

```html
<!DOCTYPE html>
<html lang="en">
<head>
<meta charset="utf-8">
<title>Corval SHS Classroom Posters</title>
<link rel="stylesheet" href="https://fonts.googleapis.com/css2?family=Montserrat:wght@500;600;700;800;900&display=swap">
<style>
:root{
  --navy:#0b3a75;
  --navy-dark:#082f61;
  --yellow:#f5e77e;
  --yellow-bright:#f2e35f;
  --sky:#e3eef8;
  --white:#ffffff;
  --red:#e0312f;
  --ink:#3c4a5e;
  --line:#9fb3cf;
}
*{box-sizing:border-box;margin:0;padding:0}
html,body{width:1200px;height:1200px;overflow:hidden;background:var(--white);font-family:"Montserrat",sans-serif}
.poster{position:absolute;top:241px;width:503px;height:711px;background:var(--white);box-shadow:0 0 3px rgba(0,0,0,.15);overflow:hidden}
.poster--steps{left:70px}
.poster--ai{left:627px}

/* shared header */
.header{position:absolute;left:0;top:0;width:100%;background:var(--navy)}
.title{position:absolute;left:162px;font-weight:900;font-size:31px;line-height:31px;color:var(--white);letter-spacing:.2px}
.title .hl{color:var(--yellow-bright)}
.brand{position:absolute;left:30px;top:34px;display:flex;align-items:center;gap:7px;font-weight:800;font-size:14px;color:var(--white);line-height:1.1}
.brand__mark{width:16px;height:16px;background:var(--yellow-bright)}

/* steps poster */
.poster--steps .header{height:114px}
.rule{position:absolute;left:0;top:114px;width:100%;height:4px;background:var(--yellow-bright)}
.band{position:absolute;left:0;top:118px;width:100%;height:52px;background:var(--sky)}
.band__text{position:absolute;left:162px;top:13px;font-weight:800;font-size:23px;color:var(--navy)}
.step{position:absolute;top:229px;width:144px;height:356px;border-radius:9px}
.step--navy{background:var(--navy);color:var(--white)}
.step--yellow{background:var(--yellow);color:var(--navy)}
.step__icon{position:absolute;top:-36px;left:34px;width:76px;height:76px;border-radius:50%;border:3px solid var(--navy)}
.step--navy .step__icon{background:var(--yellow)}
.step--yellow .step__icon{background:var(--white)}
.step__num{position:absolute;left:0;top:69px;width:34px;height:27px;border-radius:0 6px 6px 0;font-weight:800;font-size:16px;display:flex;align-items:center;justify-content:center}
.step--navy .step__num{background:var(--yellow);color:var(--navy)}
.step--yellow .step__num{background:var(--navy);color:var(--yellow)}
.step__head{position:absolute;left:43px;top:62px;font-weight:900;font-size:16px;line-height:15.5px}
.step__lead{position:absolute;left:8px;right:6px;top:129px;height:40px;border-top:1px solid rgba(255,255,255,.55);border-bottom:1px solid rgba(255,255,255,.55);padding:8px 0 0 2px;font-weight:700;font-size:8.6px;line-height:12px;white-space:nowrap;letter-spacing:-.1px}
.step--navy .step__lead{color:var(--yellow-bright)}
.step--yellow .step__lead{border-color:var(--navy)}
.ticks{position:absolute;left:16px;right:14px;top:188px;list-style:none}
.ticks li{position:relative;padding-left:16px;font-weight:700;font-size:7.8px;line-height:10px;margin-bottom:11.5px}
.ticks svg{position:absolute;left:0;top:1px;width:9px;height:9px}
.tight li{margin-bottom:11px}
.step__note{position:absolute;left:14px;font-weight:700;font-size:7.8px;line-height:10px}
.pill{position:absolute;top:600px;width:128px;height:27px;border-radius:14px;background:var(--navy);color:var(--yellow-bright);font-weight:800;font-size:12px;display:flex;align-items:center;justify-content:center}
.chev{position:absolute;top:604px;width:14px;height:20px}
.refs{position:absolute;left:30px;right:30px;top:654px;text-align:center;font-weight:700;font-size:5px;line-height:7px;color:#222;text-transform:uppercase}
.refs p{margin-bottom:6px}

/* ai poster */
.poster--ai .header{height:151px}
.foot{position:absolute;left:0;top:603px;width:100%;height:108px;background:var(--navy)}
.box{position:absolute;top:178px;width:214px;height:249px;border-radius:10px;overflow:hidden}
.box__top{position:absolute;left:0;top:0;width:100%;font-weight:800}
.box__body{position:absolute;left:0;width:100%;bottom:0;border-radius:10px}
.box--must{left:33px}
.box--must .box__top{height:60px;background:var(--yellow);color:var(--navy);font-size:16px;padding:19px 0 0 27px}
.box--must .box__body{top:51px;background:var(--navy)}
.box--help{left:263px}
.box--help .box__top{height:90px;background:var(--navy);color:var(--white);font-size:15px;line-height:15px;padding:20px 0 0 24px;white-space:nowrap}
.box--help .box__body{top:81px;background:var(--yellow)}
.box .ticks{top:20px;left:22px;right:10px}
.box .ticks li{font-weight:600;font-size:9.6px;line-height:12.8px;padding-left:21px;margin-bottom:13px}
.box .ticks svg{width:9px;height:9px;top:2px}
.box--must .ticks li{color:var(--white)}
.box--help .ticks li{color:var(--navy)}
.cannot{position:absolute;left:146px;top:446px;width:208px;height:28px;border-radius:14px;background:var(--navy);color:var(--white);font-weight:800;font-size:16px;display:flex;align-items:center;justify-content:center}
.bracket{position:absolute;left:47px;top:460px;width:411px;height:38px;border:1px solid var(--line);border-bottom:none;border-radius:8px 8px 0 0}
.card{position:absolute;top:510px;width:103px;height:127px;background:var(--white);border:1.5px solid var(--line);border-radius:8px;padding:29px 2px 0;text-align:center;font-weight:600;font-size:11.4px;line-height:15px;color:var(--ink)}
.card::after{content:"";position:absolute;left:30px;right:30px;bottom:-2px;height:3px;background:var(--yellow-bright)}
.card svg{position:absolute;left:34px;top:-18px;width:35px;height:35px}
.motto{position:absolute;left:31px;top:658px;width:440px;height:24px;border-radius:12px;background:var(--yellow-bright);color:var(--navy);font-weight:800;font-size:12px;display:flex;align-items:center;justify-content:center}
</style>
</head>
<body>
<svg width="0" height="0" style="position:absolute">
  <defs>
    <symbol id="tick-yellow" viewBox="0 0 10 10"><circle cx="5" cy="5" r="5" fill="#f2e35f"/><path d="M2.8 5.1l1.5 1.5 3-3" fill="none" stroke="#0b3a75" stroke-width="1.3"/></symbol>
    <symbol id="tick-navy" viewBox="0 0 10 10"><circle cx="5" cy="5" r="5" fill="#0b3a75"/><path d="M2.8 5.1l1.5 1.5 3-3" fill="none" stroke="#f5e77e" stroke-width="1.3"/></symbol>
    <symbol id="cross" viewBox="0 0 36 36"><circle cx="18" cy="18" r="17" fill="#e0312f" stroke="#fff" stroke-width="1.5"/><path d="M11.5 11.5l13 13M24.5 11.5l-13 13" stroke="#fff" stroke-width="4.5" stroke-linecap="round"/></symbol>
    <symbol id="chevron" viewBox="0 0 14 20"><path d="M2 2l9 8-9 8" fill="none" stroke="#f2e35f" stroke-width="4"/></symbol>
  </defs>
</svg>

<section class="poster poster--steps">
  <div class="header">
    <div class="brand"><span class="brand__mark"></span><span>Corval SHS</span></div>
    <h1 class="title" style="top:36px"><span class="hl">BEFORE YOU ASK</span><br>THE TEACHER...</h1>
  </div>
  <div class="rule"></div>
  <div class="band"><p class="band__text">TRY THESE STEPS FIRST!</p></div>

  <article class="step step--navy" style="left:24px">
    <div class="step__icon" role="img" aria-label="Icon of a head with a brain"></div>
    <div class="step__num">1</div>
    <h2 class="step__head">THINK<br>AT<br>FIRST</h2>
    <p class="step__lead">Don't give up straight<br>away.</p>
    <ul class="ticks">
      <li><svg><use href="#tick-yellow"/></svg>Read the question<br>carefully.</li>
      <li><svg><use href="#tick-yellow"/></svg>Identify what you<br>already know.</li>
      <li><svg><use href="#tick-yellow"/></svg>Try a strategy you've<br>used before.</li>
      <li><svg><use href="#tick-yellow"/></svg>Give yourself thinking<br>time.</li>
    </ul>
  </article>

  <article class="step step--yellow" style="left:180px">
    <div class="step__icon" role="img" aria-label="Icon of a checklist calendar"></div>
    <div class="step__num">2</div>
    <h2 class="step__head">CHECK<br>YOUR<br>SUPPORTS</h2>
    <p class="step__lead">Before asking for help,<br>check:</p>
    <ul class="ticks tight">
      <li><svg><use href="#tick-navy"/></svg>Learning goal and<br>success criteria.</li>
      <li><svg><use href="#tick-navy"/></svg>Worked examples.</li>
      <li><svg><use href="#tick-navy"/></svg>Class notes.</li>
      <li><svg><use href="#tick-navy"/></svg>Classroom displays.</li>
      <li><svg><use href="#tick-navy"/></svg>CLearn resources.</li>
      <li><svg><use href="#tick-navy"/></svg>Task sheet and<br>instructions.</li>
    </ul>
  </article>

  <article class="step step--navy" style="left:335px">
    <div class="step__icon" role="img" aria-label="Icon of two people with a question mark"></div>
    <div class="step__num">3</div>
    <h2 class="step__head">ASK 3<br>BEFORE<br>ME</h2>
    <p class="step__lead">Ask three sources before<br>asking the teacher:</p>
    <ul class="ticks">
      <li><svg><use href="#tick-yellow"/></svg>A person<br>(partner or neighbour)</li>
      <li><svg><use href="#tick-yellow"/></svg>A place<br>(notes, display, CLearn)</li>
      <li><svg><use href="#tick-yellow"/></svg>A resource<br>(worked example, task<br>sheet)</li>
    </ul>
    <p class="step__note" style="top:299px">Then ask the teacher if you<br>still need help.</p>
  </article>

  <div class="pill" style="left:32px">WE BELIEVE</div>
  <svg class="chev" style="left:166px"><use href="#chevron"/></svg>
  <div class="pill" style="left:188px">WE STRIVE</div>
  <svg class="chev" style="left:322px"><use href="#chevron"/></svg>
  <div class="pill" style="left:343px">WE ACHIEVE</div>

  <div class="refs">
    <p>Harlow, C. 2025. "Why students don't ask for help- and how to change that" downloaded on 24/04/2026 from<br>https://www.learnwell.example.org/article/getting-students-ask-help/</p>
    <p>ERLO, 2024. "Supporting self-regulated learning", downloaded on 24/04/2026 from<br>https://www.evidencehub.example.au/files/2024-02/supporting-self-regulated-learning.pdf</p>
  </div>
</section>

<section class="poster poster--ai">
  <div class="header">
    <div class="brand"><span class="brand__mark"></span><span>Corval SHS</span></div>
    <h1 class="title" style="top:36px"><span class="hl">USING AI</span><br>&amp; OTHER TOOLS<br>RESPONSIBLY</h1>
  </div>
  <div class="foot"></div>

  <div class="box box--must">
    <h2 class="box__top">What You Must Do:</h2>
    <div class="box__body">
      <ul class="ticks">
        <li><svg><use href="#tick-yellow"/></svg>Complete your own work</li>
        <li><svg><use href="#tick-yellow"/></svg>Demonstrate your progress<br>(drafts, notes, planning,<br>revisions)</li>
        <li><svg><use href="#tick-yellow"/></svg>Use feedback to improve<br>your work</li>
        <li><svg><use href="#tick-yellow"/></svg>Demonstrate your<br>understanding of the ideas<br>in your submission</li>
      </ul>
    </div>
  </div>

  <div class="box box--help">
    <h2 class="box__top">What AI can help you<br>do (when approved<br>by your teacher)</h2>
    <div class="box__body">
      <ul class="ticks">
        <li><svg><use href="#tick-navy"/></svg>Brainstorm ideas</li>
        <li><svg><use href="#tick-navy"/></svg>Check spelling, grammar<br>and clarity</li>
        <li><svg><use href="#tick-navy"/></svg>Read your work aloud using<br>text-to-speech tools</li>
        <li><svg><use href="#tick-navy"/></svg>Help identify areas for<br>improvement in a draft</li>
      </ul>
    </div>
  </div>

  <div class="bracket"></div>
  <h2 class="cannot">What You Cannot Do</h2>
  <div class="card" style="left:30px"><svg><use href="#cross"/></svg>Submit<br>AI<br>generated<br>work as<br>your own</div>
  <div class="card" style="left:144px"><svg><use href="#cross"/></svg>Copy &amp; paste<br>AI responses<br>without<br>acknowledging<br>or adapting<br>them</div>
  <div class="card" style="left:258px"><svg><use href="#cross"/></svg>Use<br>AI tools<br>to complete<br>the whole<br>task for you</div>
  <div class="card" style="left:373px"><svg><use href="#cross"/></svg>Submit work<br>that does not<br>demonstrate<br>your<br>understanding</div>

  <p class="motto">If you didn't create, develop and understand it, it isn't your work.</p>
</section>
</body>
</html>
```